Willow Crest Brand - Bag Design

We are a company dealing with nuts, grains and seeds and are looking for a design for our retail bag packaging that will be consistent across all our product range. We are currently differentiating in way of color but please feel free to be more creative if you wish. Sample of products include pumpkin seeds, rolled oats, almonds, etc.
Design Idea: Hygienic, Natural (from Nature), Quality & Upscale, Simple & Clean design
Target Market: High-end Markets, end-users of A/B type.
1. Bag size is 210 mm (width) * 310 mm (length). Material is OPP or multi-layer PP.
2. Front must have clear window to show packed products. Back clear window is optional.
3. Front side must have logo that stands out (Willow Crest) as attached.
4. Front side must have product name and net weight.
5. Back side must have enough space for Nutrition Fact, product descriptions (110 mm * 100 mm), and barcode.
6. Back side must have white space to print production and expiry dates about 25 mm * 30 mm.
7. Top and bottom of bag must be opaque and not show product.
Reason: Extended period for more new ideas and also for requested modification.
Target Market(s)
Premium market. Type A to B customers as well as professional clients. The product is not a snack. It is for cooking or baking.
Industry/Entity Type
Food Store
Requirements
Must have
- Look unique and stand out from others in the market.
- The colors of the word "Willow Crest" and the blue air-brush in the logo can be changed.
Nice to have
- See project description
Should not have
- See project description

```html
<!DOCTYPE html>
<html lang="en">
<head>
<meta charset="utf-8">
<title>Willow Crest – Pumpkin Seeds Bag</title>
<link rel="stylesheet" href="https://fonts.googleapis.com/css2?family=Nunito:wght@600;800;900&display=swap">
<style>
  :root {
    --page-bg: #c9c9c9;
    --bag-white: #fbfbfb;
    --yellow-deep: #f2b705;
    --yellow-light: #e9e33a;
    --purple-deep: #5a2a8a;
    --purple-mid: #6e3d9e;
    --purple-light: #ac92cf;
    --green: #1e9a52;
    --green-light: #2fb368;
    --seed-cream: #ece3cf;
    --seed-shadow: #d6c8a8;
    --text-grey: #a3a3a3;
    --white: #ffffff;
  }
  * { box-sizing: border-box; margin: 0; padding: 0; }
  html, body {
    width: 960px;
    height: 1200px;
    overflow: hidden;
    background: var(--page-bg);
    font-family: "Nunito", Arial, sans-serif;
  }
  .bag {
    position: absolute;
    left: 160px;
    top: 100px;
    width: 640px;
    height: 1000px;
  }
  .bag-art {
    position: absolute;
    inset: 0;
    width: 640px;
    height: 1000px;
  }
  .brand {
    position: absolute;
    left: 120px;
    top: 215px;
    display: flex;
    align-items: center;
    gap: 14px;
    transform: rotate(12deg);
    transform-origin: left center;
  }
  .brand-dot {
    width: 30px;
    height: 30px;
    border-radius: 50%;
    background: var(--yellow-deep);
  }
  .brand-name {
    font-weight: 800;
    font-size: 44px;
    color: var(--purple-deep);
    letter-spacing: 0.5px;
    white-space: nowrap;
  }
  .product-name {
    position: absolute;
    left: 92px;
    top: 300px;
    transform: rotate(18deg);
    transform-origin: left top;
    color: var(--white);
    font-weight: 800;
    line-height: 0.95;
  }
  .product-name .main { display: block; font-size: 50px; }
  .product-name .sub { display: block; font-size: 46px; padding-left: 140px; }
  .claim-tag {
    position: absolute;
    left: 296px;
    top: 838px;
    width: 300px;
    height: 56px;
    transform: rotate(18deg);
    transform-origin: left top;
    background: linear-gradient(90deg, var(--green), var(--green-light));
    color: var(--white);
    font-weight: 800;
    font-size: 33px;
    display: flex;
    align-items: center;
    justify-content: center;
    white-space: nowrap;
  }
  .net-weight {
    position: absolute;
    left: 79px;
    top: 932px;
    font-size: 16px;
    font-weight: 600;
    color: var(--text-grey);
  }
</style>
</head>
<body>
  <div class="bag">
    <svg class="bag-art" viewBox="0 0 640 1000" xmlns="http://www.w3.org/2000/svg">
      <defs>
        <linearGradient id="yellowBand" x1="0" y1="0" x2="1" y2="0">
          <stop offset="0" stop-color="var(--yellow-deep)"/>
          <stop offset="1" stop-color="var(--yellow-light)"/>
        </linearGradient>
        <linearGradient id="purpleBand" x1="0" y1="0" x2="1" y2="0">
          <stop offset="0" stop-color="var(--purple-deep)"/>
          <stop offset="1" stop-color="var(--purple-mid)"/>
        </linearGradient>
        <linearGradient id="banner" x1="0" y1="0" x2="1" y2="0">
          <stop offset="0" stop-color="var(--purple-deep)"/>
          <stop offset="0.55" stop-color="var(--purple-mid)"/>
          <stop offset="1" stop-color="var(--purple-light)"/>
        </linearGradient>
        <linearGradient id="seeds" x1="0" y1="0" x2="1" y2="1">
          <stop offset="0" stop-color="var(--seed-cream)"/>
          <stop offset="0.5" stop-color="#e4d9c0"/>
          <stop offset="1" stop-color="var(--seed-shadow)"/>
        </linearGradient>
      </defs>

      <rect class="bag-body" x="0" y="0" width="640" height="1000" rx="6" fill="var(--bag-white)"/>

      <polygon class="product-window" role="img" aria-label="Clear window showing the packed pumpkin seeds"
               points="79,403 640,585 640,895 79,706" fill="url(#seeds)"/>

      <polygon class="band-left-top" points="0,0 79,0 79,360 0,400" fill="url(#yellowBand)"/>
      <polygon class="band-left-bottom" points="0,400 79,360 79,1000 0,1000" fill="url(#purpleBand)"/>
      <polygon class="band-right-top" points="596,0 640,0 640,560 596,575" fill="url(#yellowBand)"/>
      <polygon class="band-right-bottom" points="596,575 640,560 640,1000 596,1000" fill="url(#purpleBand)"/>

      <polygon class="name-banner" points="79,293 482,425 465,522 79,403" fill="url(#banner)"/>
    </svg>

    <div class="brand">
      <span class="brand-dot"></span>
      <span class="brand-name">Willow Crest</span>
    </div>

    <h1 class="product-name">
      <span class="main">Pumpkin</span>
      <span class="sub">seeds</span>
    </h1>

    <div class="claim-tag">100% Natural</div>

    <p class="net-weight">Net Wt. 16 OZ (454g)</p>
  </div>
</body>
</html>
```